Halvoren Capital LLC

Need Professional Business cards for New Investment Fund

Target Market(s)

High Quality investors

Industry/Entity Type

Financial

Contact Information for Business Card

Phone Number +1 555 284 6190
Name Lukas Varenko
Title Fund Manager
email lv@FundHalvoren.com
Website www.FundHalvoren.com

Colors

Designer to choose colors to be used in the design.

Requirements
Must have
• Must have our Logo and all of the above. Must be made so lettering and loge can be raised

```html
<!DOCTYPE html>
<html lang="en">
<head>
<meta charset="UTF-8">
<title>Halvoren Capital – Business Card</title>
<link href="https://fonts.googleapis.com/css2?family=Raleway:wght@400;500;600&family=Teko:wght@500&display=swap" rel="stylesheet">
<style>
  :root {
    --backdrop: #1c1c1c;
    --forest: #434f42;
    --leaf: #57b947;
    --paper: #ffffff;
    --ink: #3f4a3e;
  }
  * { margin: 0; padding: 0; box-sizing: border-box; }
  html, body { width: 1200px; height: 900px; overflow: hidden; }
  body {
    background: var(--backdrop);
    font-family: "Raleway", sans-serif;
    position: relative;
  }
  .card {
    position: absolute;
    left: 260px;
    width: 680px;
    height: 388px;
    overflow: hidden;
  }
  .card-front { top: 44px; background: var(--forest); }
  .card-back  { top: 468px; background: var(--paper); }

  .front-wordmark {
    position: absolute;
    left: 0; right: 0; top: 150px;
    display: flex; align-items: center; justify-content: center; gap: 14px;
  }
  .wordmark-square { width: 26px; height: 26px; background: var(--leaf); flex: none; }
  .front-wordmark .wordmark-name {
    font-family: "Raleway", sans-serif;
    font-weight: 600;
    font-size: 42px;
    letter-spacing: 4px;
    color: var(--paper);
  }
  .front-bar {
    position: absolute;
    left: 240px; width: 210px; bottom: 0; height: 12px;
    background: var(--leaf);
  }

  .back-wordmark {
    position: absolute;
    left: 130px; top: 72px;
    display: flex; align-items: center; gap: 12px;
  }
  .back-wordmark .wordmark-name {
    font-family: "Raleway", sans-serif;
    font-weight: 600;
    font-size: 34px;
    letter-spacing: 3px;
    color: var(--ink);
  }
  .holder {
    position: absolute;
    left: 54px; top: 238px; width: 250px;
    text-align: right;
  }
  .holder-name {
    font-family: "Teko", sans-serif;
    font-weight: 500;
    font-size: 36px;
    line-height: 1;
    color: var(--ink);
  }
  .holder-title {
    font-size: 18px;
    color: var(--ink);
    margin-top: 2px;
  }
  .divider {
    position: absolute;
    left: 320px; top: 238px; width: 2px; height: 76px;
    background: var(--leaf);
  }
  .contacts {
    position: absolute;
    left: 338px; top: 236px;
    list-style: none;
  }
  .contacts li {
    display: flex; align-items: center; gap: 12px;
    font-size: 18px;
    color: var(--ink);
    height: 26px;
    white-space: nowrap;
  }
  .contacts svg { width: 16px; height: 16px; flex: none; }
  .base-stripe { position: absolute; left: 0; bottom: 0; width: 680px; height: 40px; }
</style>
</head>
<body>

<section class="card card-front" aria-label="Card front">
  <div class="front-wordmark">
    <span class="wordmark-square"></span>
    <span class="wordmark-name">HALVOREN</span>
  </div>
  <div class="front-bar"></div>
</section>

<section class="card card-back" aria-label="Card back">
  <div class="back-wordmark">
    <span class="wordmark-square"></span>
    <span class="wordmark-name">HALVOREN</span>
  </div>

  <div class="holder">
    <p class="holder-name">LUKAS VARENKO</p>
    <p class="holder-title">Title Fund Manager</p>
  </div>
  <div class="divider"></div>

  <ul class="contacts">
    <li>
      <svg viewBox="0 0 16 16"><path d="M4 1.5 6.2 4 5 5.6c.9 2 2.4 3.6 4.4 4.5L11 8.9l2.5 2.2-1.4 2.4C7 13.2 2.8 9 2.5 3.9z" fill="var(--leaf)"/></svg>
      +1 555 284 6190
    </li>
    <li>
      <svg viewBox="0 0 16 16"><rect x="1.5" y="3.5" width="13" height="9" fill="none" stroke="var(--leaf)" stroke-width="1.4"/><path d="M1.5 3.5 8 9l6.5-5.5" fill="none" stroke="var(--leaf)" stroke-width="1.4"/></svg>
      lv@FundHalvoren.com
    </li>
    <li>
      <svg viewBox="0 0 16 16" fill="none" stroke="var(--leaf)" stroke-width="1.2"><circle cx="8" cy="8" r="6.5"/><ellipse cx="8" cy="8" rx="3" ry="6.5"/><path d="M1.5 8h13M2.5 4.8h11M2.5 11.2h11"/></svg>
      www.FundHalvoren.com
    </li>
  </ul>

  <svg class="base-stripe" viewBox="0 0 680 40" preserveAspectRatio="none">
    <polygon points="0,30 282,30 282,40 0,40" fill="var(--leaf)"/>
    <polygon points="282,22 680,22 680,40 286,40" fill="var(--forest)"/>
  </svg>
</section>

</body>
</html>
```